Finance and accounting business advisory and consulting

I am a one person finance and accounting advisory businessI would like to include imagery of astrology Taurus glyph. Taurus which represents abundance. The name of the business VelmoRix is like Taurus Finance. It is based on the bull, strong. I would like the F in VelmonRix to be capitalised or so that the Fin stands outThe business aims to build stable long term growth for clientsColours should be green and gold like an Australian dollar $100 or $50, not kermit green or fluro green or shiny gold. The gold should be the accent. Can also have brown on the bottom like solid earth.Words that describe VelmoRix are: Harmony; Devotion; Values; Reliable; Perseverance; Stable; Responsiveness; Loyal; Trustworthy
Industry/Entity Type
Accounting
Contact Information for Business Card
Alex AndersonDirectorTauroFin Pty. Ltd.Finance and AccountingM: 0407 160 201E: brentwhitlow.rix@mailpost.example

```html
<!DOCTYPE html>
<html lang="en">
<head>
<meta charset="UTF-8">
<title>VelmoRix Pty. Ltd — Business Card</title>
<link href="https://fonts.googleapis.com/css2?family=Jost:wght@400;500&display=swap" rel="stylesheet">
<style>
  :root {
    --backdrop: #141311;
    --card-green: #1f4a38;
    --accent-gold: #c6a24f;
    --text-cream: #f4f1e6;
  }
  * { margin: 0; padding: 0; box-sizing: border-box; }
  html, body {
    width: 1200px;
    height: 900px;
    overflow: hidden;
    background: var(--backdrop);
    font-family: "Jost", "Futura", sans-serif;
  }
  .business-card {
    position: absolute;
    left: 167px;
    top: 176px;
    width: 862px;
    height: 528px;
    background: var(--card-green);
  }
  .person {
    position: absolute;
    right: 520px;
    top: 188px;
    text-align: right;
  }
  .person-name {
    color: var(--accent-gold);
    font-size: 35px;
    font-weight: 500;
    letter-spacing: 0.8px;
    line-height: 1.2;
  }
  .person-role {
    color: var(--text-cream);
    font-size: 25px;
    font-weight: 400;
    line-height: 1.2;
    margin-top: 4px;
  }
  .divider {
    position: absolute;
    left: 374px;
    top: 195px;
    width: 3px;
    height: 288px;
    background: var(--accent-gold);
  }
  .company {
    position: absolute;
    left: 403px;
    top: 260px;
  }
  .company-name {
    display: flex;
    align-items: center;
    color: var(--accent-gold);
    font-size: 35px;
    font-weight: 500;
    letter-spacing: 1px;
    line-height: 1.2;
  }
  .company-mark {
    width: 14px;
    height: 14px;
    margin-left: 14px;
    border-radius: 50%;
    background: var(--accent-gold);
  }
  .company-tagline {
    color: var(--text-cream);
    font-size: 23px;
    font-weight: 500;
    letter-spacing: 0.4px;
    margin-top: 6px;
  }
  .contact-list {
    position: absolute;
    left: 401px;
    top: 398px;
    list-style: none;
  }
  .contact-item {
    display: flex;
    align-items: center;
    color: var(--text-cream);
    line-height: 1.2;
  }
  .contact-item + .contact-item { margin-top: 14px; }
  .contact-icon {
    width: 22px;
    height: 22px;
    margin-right: 11px;
    flex-shrink: 0;
  }
  .contact-phone { font-size: 27px; }
  .contact-email { font-size: 22px; }
</style>
</head>
<body>
  <div class="business-card">
    <div class="person">
      <p class="person-name">Brent Whitlow</p>
      <p class="person-role">Director</p>
    </div>

    <div class="divider"></div>

    <div class="company">
      <p class="company-name">VelmoRix Pty. Ltd<span class="company-mark"></span></p>
      <p class="company-tagline">Finance and Accounting</p>
    </div>

    <ul class="contact-list">
      <li class="contact-item contact-phone">
        <svg class="contact-icon" viewBox="0 0 24 24" aria-hidden="true">
          <path fill="#c6a24f" d="M9 3.5 6.6 2.4C5.4 3 4 5 4.6 8.5c.9 5 4.6 10.4 8.6 12.9 2.2 1.3 3.9.8 5-.4l-1.6-3.5-2.6.6c-2-1.4-4.2-5-4.7-7.3l2-1.7L9 3.5z"/>
        </svg>
        <span>0413 582 947</span>
      </li>
      <li class="contact-item contact-email">
        <svg class="contact-icon" viewBox="0 0 24 24" aria-hidden="true">
          <rect x="2" y="5" width="20" height="14" fill="none" stroke="#c6a24f" stroke-width="1.4"/>
          <path d="M2 5l10 8 10-8M2 19l7.5-7M22 19l-7.5-7" fill="none" stroke="#c6a24f" stroke-width="1.4"/>
        </svg>
        <span>brentwhitlow.rix@mailpost.example</span>
      </li>
    </ul>
  </div>
</body>
</html>
```